IT Company needs Website for new Web and Mobile products for Sports and Fitness

Background:

We developed web based white label frontend web solution, backend services and white label mobile apps for to log, analyze, share and control sport and fitness activities. The name of this product suite is "Trevantix" (http://trevantix-example.com)

This products will be used by customers that provide platforms and community systems for sport and fitness. One of the major USP's is, that our technology i open for nearly all common formats, devices and apps out in the market. This means, you can just upload your data directly from device, file or app - e.G. Kestrel, Bolvane, Ravelo, StrideVault, Pacelumo, Zembra and much others.

Two current concrete examples/References

(1) MyQuorel
It's an international platform from quorel for runners. It provides individual training lans and a training log. MyQuorel uses the Backend Product "Trevantix Hub" (see http://hub.trevantix-example.net for a landing page) to integrate device, file and app support. Before this, every user has to track his training with manual inputs

(2) Paceharbor and fen-zine
Both are German customers. Paceharor is focused on runners. fen-zine is focused on Triatheletes. Both use the Product "Trevantix Web". This is a complete web solution with web based frontend solutions for athletes and coaches.

What do we need?
We need website layout for B2B for our products. We don't need lot's of pages. We need the pretty and nice layout, so we can derive the pages we need.

IMPORTANT
We don't talk about the webpages for the product itself (this will be a different project in future). We talk about a website, explaining the products)
Updates

Hi all,

we just start reviewing the first designs, and try to give feedback as detailed as possible. We attached a PDF document, to describe the the products a little bit more detailed. 

As written in the description, in the end we have two different sections. One is the usual stuff like "start page", "about", "contact", "disclaimer", "pricing", "blah...." and one will be the Developer Section, the "Tec Section". This ist aimed to developers (of our customers) that will integrate our products in there existing system or which will integrate our services in there own software.  This "pages" are more like "documentation", so easy to read and cool to look at (cause developers likes it cool, but straight)

Dear all,

we just do the final review. Cause this week is with heavy load, it takes some time...

Cheers

Odell

Target Market(s)

* Platforms and Communities for sport, health and fitness
* Gyms

Industry/Entity Type

Concrete

Font styles to use
Sans Serif

Requirements
Must have
• * Templates shall base on bootstrap. If not, it shall be easily realized on our site with bootstrap or out of the box "full responsive"

* HTML5 / CSS3
Nice to have
• PAGES
- Start Page
- Generic Template (from which we can derive additional pages)
- Contact Page
- Disclaimer Page
- Blog/News Page
- "About us" Page (can be combined with disclaimer)
- One Example product page (in end we have 3 products), shall show (if you need product details, let me know)
- product and it's description
- pricing information
- Add-Ons for the product
- Developer Section Page (Start Point for developers, where the finde "basic technical concepts and developer API's
- Example Developer Page for technical concept
- Example Developer Page for API

LOGO ISSUE
You can use an align to the Logo attached OR provide a new logo. The given logo is a logo for our own B2C Website http://trevantix-example.net. It's not really necessary, that the logo or the color must be used for the product website. Maybe it will be better if it's a complete new one, to avoid irritation between Trevantix as a B2B product and trevantix-example.net as a B2C platform.
Should not have
• No Flash and other proprietary technologies

```html
<!DOCTYPE html>
<html lang="en">
<head>
<meta charset="utf-8">
<title>Trevantix – Digital Sport and Fitness Services</title>
<link href="https://fonts.googleapis.com/css2?family=Source+Sans+3:wght@400;600;700&display=swap" rel="stylesheet">
<style>
:root{
  --orange:#f08a12;
  --orange-dark:#d9720a;
  --ink:#2b2b2b;
  --text:#555;
  --muted:#888;
  --red:#d8141b;
  --rule:#e3e3e3;
  --band:#f2f2f2;
  --stage:#ececec;
  --white:#fff;
}
*{box-sizing:border-box;margin:0;padding:0}
html,body{width:705px;height:1200px;overflow:hidden}
body{background:var(--stage);font-family:"Source Sans 3",sans-serif;color:var(--text)}
.site{position:absolute;left:0;top:134px;width:705px;height:932px;background:var(--white);overflow:hidden}

/* header */
.header{position:absolute;left:0;top:0;width:100%;height:60px}
.brand{position:absolute;left:57px;top:10px}
.brand-mark{display:flex;align-items:center;gap:6px}
.brand-dot{width:16px;height:16px;border-radius:50%;background:var(--orange)}
.brand-name{font-size:20px;font-weight:600;color:var(--ink);line-height:1}
.brand-tag{font-size:6px;font-weight:700;color:var(--ink);letter-spacing:.2px;margin-top:6px}
.nav{position:absolute;left:232px;top:24px;display:flex;font-size:7px;color:#666;text-transform:uppercase}
.nav span{padding:0 19px;border-left:1px solid var(--rule);line-height:12px}
.nav span:first-child{border-left:0;padding-left:0}

/* hero */
.hero{position:absolute;left:0;top:60px;width:100%;height:295px;
  background:radial-gradient(ellipse at 25% 40%,#fff3d6 0%,#f9c874 30%,#e79a3a 60%,#b7662a 100%)}
.hero-photo{position:absolute;right:0;top:0;width:320px;height:295px;
  background:linear-gradient(160deg,rgba(160,80,40,.35),rgba(120,50,30,.55))}
.hero-title{position:absolute;left:57px;top:89px;font-size:20px;line-height:26px;font-weight:400;color:#3a3a3a;text-transform:uppercase}
.hero-title .accent{color:var(--orange)}
.signup{position:absolute;left:57px;top:152px;display:flex;height:26px}
.signup-input{width:173px;background:#fafafa;border:1px solid #ddd;font-size:7px;color:#999;padding:0 8px;line-height:24px}
.signup-btn{width:92px;background:linear-gradient(#f4a12c,var(--orange-dark));color:#fff;font-size:9px;text-align:center;line-height:26px;border-radius:2px}
.hero-arrow{position:absolute;top:127px;width:22px;height:22px;border-radius:50%;border:1px solid rgba(255,255,255,.5)}
.hero-arrow.left{left:-11px}.hero-arrow.right{right:-11px}
.hero-dots{position:absolute;left:610px;top:280px;display:flex;gap:4px}
.hero-dots i{width:6px;height:6px;border-radius:50%;background:rgba(255,255,255,.5)}
.hero-dots i:first-child{background:#fff}

/* welcome */
.welcome{position:absolute;left:79px;top:380px;width:353px}
.section-title{font-size:14px;font-weight:700;color:var(--ink)}
.section-title .accent{color:var(--orange)}
.copy{font-size:6.6px;line-height:12.7px;color:var(--text)}
.welcome .copy{margin-top:9px}
.more{font-size:7px;color:var(--red);font-weight:600}
.welcome .more{position:absolute;right:0;top:106px}
.references{position:absolute;left:465px;top:380px;width:182px}
.references h3{font-size:8px;font-weight:600;color:var(--ink)}
.ref-grid{display:grid;grid-template-columns:78px 78px;gap:10px 12px;margin-top:10px}
.ref{height:34px;border:1px solid #ddd;border-radius:3px;display:flex;align-items:center;justify-content:center;font-size:12px;font-weight:700;color:#2c3a73}
.references .more{position:absolute;right:0;top:106px}
.divider{position:absolute;left:79px;top:500px;width:568px;height:1px;background:var(--rule)}

/* feature */
.monitor{position:absolute;left:79px;top:545px;width:167px;height:98px}
.monitor-screen{position:absolute;left:0;top:0;width:167px;height:88px;background:#111;border-radius:4px;padding:5px}
.monitor-screen div{width:100%;height:100%;background:linear-gradient(90deg,#7a5a3a,#e5b071 60%,#8a6a48)}
.monitor-stand{position:absolute;left:66px;top:88px;width:36px;height:10px;background:linear-gradient(#ccc,#eee)}
.feature{position:absolute;left:265px;top:543px;width:383px}
.feature h2{font-size:11px;font-weight:400;color:var(--ink);margin-bottom:4px}
.downloads{position:absolute;left:274px;top:647px;display:flex;gap:0}
.dl{display:flex;align-items:center;gap:6px;width:125px;font-size:6.6px;line-height:10px;color:var(--ink)}
.dl-icon{width:16px;height:16px;border-radius:50%;background:#444}

/* products */
.products{position:absolute;left:0;top:709px;width:100%;height:223px;background:var(--band)}
.products h2{position:absolute;left:79px;top:9px;font-size:13px;font-weight:400;font-variant:small-caps;color:var(--ink)}
.product{position:absolute;top:40px;width:118px}
.product h3{font-size:12px;font-weight:600;font-variant:small-caps;color:var(--ink)}
.product-img{width:113px;height:66px;margin-top:6px}
.product .copy{margin-top:6px;line-height:10px}
.product .more{position:absolute;top:146px;left:0}
.products-next{position:absolute;left:623px;top:115px}
</style>
</head>
<body>
<main class="site">
  <header class="header">
    <div class="brand">
      <div class="brand-mark"><span class="brand-dot"></span><span class="brand-name">Trevantix</span></div>
      <div class="brand-tag">DIGITAL SPORT AND FITNESS SERVICES</div>
    </div>
    <nav class="nav">
      <span>Home</span><span>Trevantix</span><span>Fitness Cloud</span><span>References</span><span>Products</span><span>Services</span>
    </nav>
  </header>

  <section class="hero">
    <div class="hero-photo" role="img" aria-label="Runner's legs in red running shoes on a sunlit road"></div>
    <span class="hero-arrow left"></span><span class="hero-arrow right"></span>
    <h1 class="hero-title"><span class="accent">Die offene Sport- und</span><br>Fitnessplatform fur jeden Sport</h1>
    <div class="signup"><div class="signup-input">WHAT'S YOUR EMAIL ADDRESS :</div><div class="signup-btn">JOIN FOR FREE</div></div>
    <div class="hero-dots"><i></i><i></i></div>
  </section>

  <section class="welcome">
    <h2 class="section-title">Welcome to <span class="accent">Trevantix</span></h2>
    <p class="copy">Sed ut perspiciatis unde omnis iste natus error sit voluptatem accusantium doloremque laudantium, totam rem aperiam, eaque ipsa quae ab illo inventore veritatis et quasi architecto beatae vitae dicta sunt explicabo. Nemo enim ipsam voluptatem quia voluptas sit aspernatur aut odit aut fugit, sed quia consequuntur magni dolores eos qui ratione voluptatem sequi nesciunt. Neque porro quisquam est, qui dolorem ipsum quia dolor sit amet, consectetur, adipisci velit, sed quia non numquam eius modi tempora incidunt ut labore et dolore magnam aliquam quaerat voluptatem aliquid ex ea commodi consequatur.</p>
    <span class="more">More</span>
  </section>
  <aside class="references">
    <h3>References</h3>
    <div class="ref-grid">
      <div class="ref">quorel</div><div class="ref">Paceharbor</div>
      <div class="ref">fen-zine</div><div class="ref">Veltor</div>
    </div>
    <span class="more">More</span>
  </aside>
  <div class="divider"></div>

  <div class="monitor">
    <div class="monitor-screen"><div role="img" aria-label="Runners jogging at sunset shown on a desktop monitor"></div></div>
    <div class="monitor-stand"></div>
  </div>
  <section class="feature">
    <h2>Neque Porro Quisquam Est</h2>
    <p class="copy">Sed ut perspiciatis unde omnis iste natus error sit voluptatem accusantium doloremque laudantium, totam rem aperiam, eaque ipsa quae ab illo inventore veritatis et quasi architecto beatae vitae dicta sunt explicabo. Nemo enim ipsam voluptatem quia voluptas sit aspernatur aut odit aut fugit, sed quia consequuntur magni dolores eos qui ratione voluptatem sequi nesciunt. Neque porro quisquam est, qui dolorem ipsum quia dolor sit amet, consectetur, adipisci velit, sed quia non numquam eius modi tempora incidunt ut labore et dolore magnam aliquam quaerat voluptatem aliquid ex ea commodi consequatur.</p>
  </section>
  <div class="downloads">
    <div class="dl"><span class="dl-icon"></span><span>Download for<br>Fenstra</span></div>
    <div class="dl"><span class="dl-icon"></span><span>Download for<br>Tuxora</span></div>
    <div class="dl"><span class="dl-icon"></span><span>Download for<br>Mobiles</span></div>
  </div>

  <section class="products">
    <h2>Products</h2>
    <article class="product" style="left:79px">
      <h3>Trevantix Hub</h3>
      <div class="product-img" role="img" aria-label="Baseball players on a field" style="background:linear-gradient(#8a7a5a,#b29c70)"></div>
      <p class="copy">Backend Data Services<br>Business Model<br>On-Demand or Dedicated</p>
      <span class="more">More</span>
    </article>
    <article class="product" style="left:215px">
      <h3>Trevantix Web</h3>
      <div class="product-img" role="img" aria-label="Sports web app on a television screen" style="background:linear-gradient(#2d3a4a,#3f7a3a)"></div>
      <p class="copy">User Services (Web) for athletes and coaches<br>White Label<br>Business Model<br>On-Demand or Dedicated</p>
      <span class="more">More</span>
    </article>
    <article class="product" style="left:346px">
      <h3>DCA</h3>
      <div class="product-img" role="img" aria-label="Aerial view of a large office building" style="background:linear-gradient(#8c8f8a,#a9aaa0)"></div>
      <p class="copy">Retrieve Data from devices<br>Direct accessible via Webbrowser<br>Mobile Agent planned for 2014</p>
      <span class="more">More</span>
    </article>
    <article class="product" style="left:482px">
      <h3>Mobile App</h3>
      <div class="product-img" role="img" aria-label="Fitness tracker app on a smartphone" style="background:linear-gradient(90deg,#111,#dcdcdc 30%,#eee 80%,#111)"></div>
      <p class="copy">Sports &amp; Fitness Tracker<br>Mobile Add-On to Trevantix Web<br>Supports external sensors<br>Available for Andrix and Iovo</p>
      <span class="more">More</span>
    </article>
    <svg class="products-next" width="8" height="14" viewBox="0 0 8 14"><path d="M0 0 L8 7 L0 14 Z" fill="#111"/></svg>
  </section>
</main>
</body>
</html>
```